Tandem Hearth Works Pty Ltd

We need business cards for a company based in Perth, we install, service and maintain fire equipment.
On the front we want a great design with our logo and a small spot for our full company name, general company email address and (08) 6120 4471. On the back we need space for our name, title, mobile number and email address on the back.

Target Market(s)

Facility managers and commercial/industrial building owners/occupiers.

Contact Information for Business Card

Font styles to use
Sans Serif

Requirements
Must have
• Please only submit 5 of your best samples.
Darker tones are preferred.
Nice to have
• We want to use, black, red and grey. Keep it modern and clean.
I've attached the company logo and a sample of a boarder we use on our emergency plans.
Should not have
• No preference. Let the designer choose.

```html
<!DOCTYPE html>
<html lang="en">
<head>
<meta charset="utf-8">
<title>Tandem Hearth Works Pty Ltd – Business Cards</title>
<link href="https://fonts.googleapis.com/css2?family=Poppins:wght@400;500;700&display=swap" rel="stylesheet">
<style>
  :root {
    --backdrop: #1e1e1e;
    --card: #ffffff;
    --brand-red: #ff0000;
    --brand-grey: #757575;
    --ink: #111111;
    --rule: #222222;
  }
  * { box-sizing: border-box; margin: 0; padding: 0; }
  html, body { width: 1200px; height: 880px; overflow: hidden; }
  body {
    background: var(--backdrop);
    font-family: "Poppins", sans-serif;
    position: relative;
  }
  .card {
    position: absolute;
    width: 520px;
    height: 300px;
    background: var(--card);
    border-radius: 14px;
    overflow: hidden;
    box-shadow: 0 18px 40px rgba(0,0,0,0.55);
  }
  .card--front { left: 80px; top: 90px; }
  .card--back  { left: 600px; top: 490px; }

  .edge-band {
    position: absolute;
    left: 0;
    width: 520px;
    height: 30px;
  }
  .edge-band--top { top: 0; }
  .edge-band--bottom { bottom: 0; transform: scaleY(-1); }
  .edge-band .band-grey { fill: var(--brand-grey); }
  .edge-band .band-red { fill: var(--brand-red); }

  .brand-mark {
    display: flex;
    align-items: center;
    gap: 10px;
  }
  .brand-mark__square {
    flex: none;
    background: var(--brand-red);
  }
  .brand-name {
    color: var(--brand-red);
    font-weight: 700;
    line-height: 1.05;
    letter-spacing: -0.5px;
  }

  .card--front .brand-mark {
    position: absolute;
    left: 0; right: 0; top: 92px;
    justify-content: center;
  }
  .card--front .brand-mark__square { width: 30px; height: 30px; }
  .card--front .brand-name { font-size: 32px; }

  .front-details {
    position: absolute;
    left: 0; right: 0; top: 170px;
    text-align: center;
    color: var(--ink);
  }
  .front-details__legal {
    font-size: 12px;
    font-weight: 500;
    letter-spacing: 1.5px;
    text-transform: uppercase;
    margin-bottom: 10px;
  }
  .front-details__row {
    display: flex;
    justify-content: center;
    gap: 22px;
    font-size: 11.5px;
  }
  .front-details__row .contact__line { line-height: 1.4; }

  .card--back .brand-mark {
    position: absolute;
    left: 28px; top: 116px;
    width: 230px;
    gap: 9px;
  }
  .card--back .brand-mark__square { width: 22px; height: 22px; align-self: flex-start; margin-top: 6px; }
  .card--back .brand-name { font-size: 26px; }

  .divider {
    position: absolute;
    left: 268px; top: 70px;
    width: 1px; height: 150px;
    background: var(--rule);
  }
  .contact {
    position: absolute;
    left: 288px; top: 64px;
    width: 220px;
    color: var(--ink);
  }
  .contact__name {
    color: var(--brand-red);
    font-weight: 700;
    font-size: 19px;
    text-transform: uppercase;
    line-height: 1.1;
  }
  .contact__title {
    font-size: 12px;
    margin-bottom: 12px;
  }
  .contact__address {
    font-size: 11px;
    line-height: 1.35;
    margin-bottom: 8px;
  }
  .contact__line {
    display: flex;
    align-items: center;
    gap: 7px;
    font-size: 11.5px;
    line-height: 1.7;
  }
  .contact__icon { width: 13px; height: 13px; flex: none; }
  .contact__icon .icon-disc { fill: var(--brand-red); }
  .contact__icon .icon-glyph { fill: #ffffff; stroke: none; }
  .contact__icon .icon-stroke { fill: none; stroke: #ffffff; stroke-width: 1.2; }
</style>
</head>
<body>

  <section class="card card--front" aria-label="Business card front">
    <svg class="edge-band edge-band--top" viewBox="0 0 520 30" preserveAspectRatio="none" aria-hidden="true">
      <polygon class="band-grey" points="0,0 520,0 520,12 450,24 360,14 270,26 180,16 90,28 0,19"/>
      <polygon class="band-red" points="0,0 520,0 520,5 480,9 400,19 310,8 220,20 130,10 40,22 0,14"/>
    </svg>

    <div class="brand-mark">
      <span class="brand-mark__square" aria-hidden="true"></span>
      <span class="brand-name">Tandem Hearth Works</span>
    </div>

    <div class="front-details">
      <p class="front-details__legal">Tandem Hearth Works Pty Ltd</p>
      <div class="front-details__row">
        <p class="contact__line">
          <svg class="contact__icon" viewBox="0 0 14 14" aria-hidden="true">
            <circle class="icon-disc" cx="7" cy="7" r="7"/>
            <path class="icon-glyph" d="M4.6 3.6l1.3-.3.7 1.8-.9.6c.4.9 1 1.6 1.9 2l.6-.9 1.8.7-.3 1.3c-2.9.2-5.3-2.3-5.1-5.2z"/>
          </svg>
          (08) 6120 4471
        </p>
        <p class="contact__line">
          <svg class="contact__icon" viewBox="0 0 14 14" aria-hidden="true">
            <circle class="icon-disc" cx="7" cy="7" r="7"/>
            <rect class="icon-stroke" x="3.6" y="4.6" width="6.8" height="4.8"/>
            <path class="icon-stroke" d="M3.6 4.6L7 7.3l3.4-2.7"/>
          </svg>
          office@tandemhearth.au
        </p>
      </div>
    </div>

    <svg class="edge-band edge-band--bottom" viewBox="0 0 520 30" preserveAspectRatio="none" aria-hidden="true">
      <polygon class="band-grey" points="0,0 520,0 520,19 430,28 340,15 250,26 160,13 70,24 0,12"/>
      <polygon class="band-red" points="0,0 520,0 520,13 470,22 380,10 290,21 200,8 110,19 0,5"/>
    </svg>
  </section>

  <section class="card card--back" aria-label="Business card back">
    <div class="brand-mark">
      <span class="brand-mark__square" aria-hidden="true"></span>
      <span class="brand-name">Tandem Hearth Works</span>
    </div>
    <div class="divider"></div>
    <div class="contact">
      <p class="contact__name">Nora Castell</p>
      <p class="contact__title">Director</p>
      <p class="contact__address">PO Box 418 Kestrel Lane<br>9 Harbour Row, Perth</p>
      <p class="contact__line">
        <svg class="contact__icon" viewBox="0 0 14 14" aria-hidden="true">
          <circle class="icon-disc" cx="7" cy="7" r="7"/>
          <path class="icon-glyph" d="M4.6 3.6l1.3-.3.7 1.8-.9.6c.4.9 1 1.6 1.9 2l.6-.9 1.8.7-.3 1.3c-2.9.2-5.3-2.3-5.1-5.2z"/>
        </svg>
        0400 118 274
      </p>
      <p class="contact__line">
        <svg class="contact__icon" viewBox="0 0 14 14" aria-hidden="true">
          <circle class="icon-disc" cx="7" cy="7" r="7"/>
          <rect class="icon-stroke" x="3.6" y="4.6" width="6.8" height="4.8"/>
          <path class="icon-stroke" d="M3.6 4.6L7 7.3l3.4-2.7"/>
        </svg>
        hello@tandemhearth.au
      </p>
    </div>
    <svg class="edge-band edge-band--bottom" viewBox="0 0 520 30" preserveAspectRatio="none" aria-hidden="true">
      <polygon class="band-grey" points="0,0 520,0 520,19 430,28 340,15 250,26 160,13 70,24 0,12"/>
      <polygon class="band-red" points="0,0 520,0 520,13 470,22 380,10 290,21 200,8 110,19 0,5"/>
    </svg>
  </section>

</body>
</html>
```